To design a brand identity that is simple and creative with 'Corvane' as the brand name, I like modern simple fonts like helvetica neue, I want to print both sides of the card, I am open to dark front and white back, but the design needs to transfer well to letter heads and email signatures, I am looking for sophisticated and elegant, but open minded about clever and off the wall, I do not do 'boring' Corvane Ventures is the mother company for a small group, specialising in Management & consulting, Software development and construction, we have a high level of integrity, we are transparent and accountable for what we do. my images are provided as a guide only, Im not expecting them to be just copied, Im looking for a creator and passionate thinker, who will put life into their work.

Target Market(s)

usually business minded people who are looking for something different in me, such as leadership, confidence and focus with thinking that is per haps a little outside the box..

Industry/Entity Type

Construction

Requirements
Must have
• clean, minmalistic
Nice to have
• custom logo
Should not have
• boring, traditional

```html
<!DOCTYPE html>
<html lang="en">
<head>
<meta charset="utf-8">
<title>Corvane Ventures – Business Card</title>
<link href="https://fonts.googleapis.com/css2?family=Open+Sans:wght@400;600;700&display=swap" rel="stylesheet">
<style>
  :root {
    --canvas: #ecebe8;
    --card-dark: #000000;
    --card-light: #ffffff;
    --brand-orange: #f0682e;
    --tagline-grey: #8a8a8a;
    --name-gold: #f5b400;
    --text-light: #ffffff;
    --service-coral: #f0595a;
    --bullet-grey: #9a9a9a;
    --web-dark: #2b2b2b;
    --divider: #8c8c8c;
    --band-top: #ffb21a;
    --band-upper: #ff3d1f;
    --band-mid: #e0245a;
    --band-lower: #8e2f7e;
    --band-bottom: #169a8e;
    --mark-fill: #f0682e;
  }
  * { margin: 0; padding: 0; box-sizing: border-box; }
  html, body {
    width: 1200px; height: 720px; overflow: hidden;
    background: var(--canvas);
  }
  .canvas {
    position: relative; width: 1200px; height: 720px;
    display: flex; align-items: center; justify-content: center; gap: 40px;
  }
  .card {
    position: relative; width: 540px; height: 309px; overflow: hidden;
    box-shadow: 0 6px 22px rgba(0,0,0,0.18);
  }

  /* Front – dark */
  .card--front { background: var(--card-dark); }
  .colour-band {
    position: absolute; left: 0; top: 0; bottom: 0; width: 132px;
    background: linear-gradient(180deg, var(--band-top) 0%, var(--band-upper) 30%, var(--band-mid) 55%, var(--band-lower) 75%, var(--band-bottom) 100%);
    border-right: 3px solid var(--divider);
  }
  .brand-mark {
    position: absolute; border-radius: 50%;
    background: var(--mark-fill);
  }
  .card--front .brand-mark {
    left: 36px; top: 52px; width: 58px; height: 58px;
    background: var(--card-dark);
  }
  .wordmark {
    position: absolute; font-family: "Open Sans", sans-serif; font-weight: 600;
    color: var(--brand-orange); line-height: 1; letter-spacing: 0.5px;
  }
  .tagline {
    position: absolute; font-family: "Open Sans", sans-serif; font-weight: 400;
    color: var(--tagline-grey); line-height: 1; letter-spacing: 1px;
  }
  .card--front .wordmark { left: 154px; top: 24px; font-size: 50px; }
  .card--front .tagline { left: 157px; top: 88px; font-size: 14px; }
  .person {
    position: absolute; right: 28px; top: 118px; text-align: right;
    font-family: "Open Sans", sans-serif;
  }
  .person__name { color: var(--name-gold); font-weight: 700; font-size: 19px; line-height: 1.1; }
  .person__title { color: var(--text-light); font-size: 13px; margin-top: 2px; margin-right: 2px; }
  .contact {
    position: absolute; left: 152px; top: 196px;
    font-family: "Open Sans", sans-serif; font-size: 13px; color: var(--text-light);
    list-style: none;
  }
  .contact li { display: flex; align-items: center; gap: 6px; height: 20px; }
  .contact li.contact__address { margin-top: 20px; }
  .contact svg { width: 12px; height: 12px; flex: none; }

  /* Back – light */
  .card--back { background: var(--card-light); }
  .card--back .brand-mark { left: 104px; top: 94px; width: 62px; height: 62px; }
  .card--back .wordmark { left: 186px; top: 88px; font-size: 64px; }
  .card--back .tagline { left: 190px; top: 168px; font-size: 15px; }
  .services {
    position: absolute; left: 0; right: 0; top: 208px; text-align: center;
    font-family: "Open Sans", sans-serif; font-size: 13px; font-weight: 600;
    color: var(--service-coral); text-transform: uppercase; letter-spacing: 0.2px;
    list-style: none; line-height: 20px;
  }
  .services li { display: inline; margin: 0 6px; }
  .services li::before {
    content: ""; display: inline-block; width: 5px; height: 5px; border-radius: 50%;
    background: var(--bullet-grey); margin-right: 4px; vertical-align: middle;
  }
  .website {
    position: absolute; left: 0; right: 0; top: 262px; text-align: center;
    font-family: "Open Sans", sans-serif; font-size: 17px; color: var(--web-dark);
    letter-spacing: 4px;
  }
</style>
</head>
<body>
<main class="canvas">

  <section class="card card--front" aria-label="Card front">
    <div class="colour-band"></div>
    <div class="brand-mark" aria-hidden="true"></div>
    <div class="wordmark">Corvane</div>
    <div class="tagline">building what comes next</div>
    <div class="person">
      <div class="person__name">Your Name</div>
      <div class="person__title">Title</div>
    </div>
    <ul class="contact">
      <li>
        <svg viewBox="0 0 12 12" aria-hidden="true"><circle cx="6" cy="6" r="6" fill="#f5b400"/><path d="M4 3.2 L5 3 L5.6 4.6 L5 5.2 Q5.6 6.5 6.8 7 L7.4 6.4 L9 7 L8.8 8 Q6.5 8.6 4.6 6.6 Q3.3 5 4 3.2Z" fill="#000"/></svg>
        +61 0400 555 012
      </li>
      <li>
        <svg viewBox="0 0 12 12" aria-hidden="true"><circle cx="6" cy="6" r="6" fill="#f5b400"/><rect x="3" y="4" width="6" height="4.2" fill="#000"/><path d="M3 4 L6 6.4 L9 4" stroke="#f5b400" stroke-width="0.8" fill="none"/></svg>
        names@corvane.ventures
      </li>
      <li class="contact__address">PO Box 118 Perth 6000</li>
    </ul>
  </section>

  <section class="card card--back" aria-label="Card back">
    <div class="brand-mark" aria-hidden="true"></div>
    <div class="wordmark">Corvane</div>
    <div class="tagline">building what comes next</div>
    <ul class="services">
      <li>Management &amp; Consulting</li><li>Software Development</li><br><li>Construction</li>
    </ul>
    <div class="website">www.corvane.com</div>
  </section>

</main>
</body>
</html>
```